Financial Services Consultant needs a business card

We need a business card for a new consulting company based in Melbourne called
"Quelbrook Insights". Tagline is Measure, Monitor, Save
We would like to see business card designs that are in line with the minimal style of the website www.quelbrook-insights.example
The font I have used on the website is Proxima Nova and would like the same or similar font used on the business card with a minimal design in line with the website Two sided with "QUELBROOK INSIGHTS" MEASURE, MONITOR, SAVE on one side and name, title and contact details on the otther
Updates

Hi All, thanks for your submissions, much appreciated.

I have recently added some colour to my webiste, it is hex #3a7b74 for those that wish to use it
Thanks

Hi all

thanks very much for your design submissions I am very impressed and they are much appreciated.

Interms of general feedback please find below;

Colour: I am trying to stick to a minimal design and colour scheme for my website which is still under construction, up to 3 colours( www.quelbrook-insights.example) it is currently black and white with a small amount of blue/green but I am open to suggestion/interpretations for a consulting company.

Card: I dont mind if it has rounded edges or straight, I was thinking about using a letterpress card if possible

Detail: the detail on the card will include; Name, Title, Mobile, Personal Email, Business Email,Web,Business Address

Once again thanks for submissions

Industry/Entity Type

Business

```html
<!DOCTYPE html>
<html lang="en">
<head>
<meta charset="utf-8">
<title>Quelbrook Insights – Business Card</title>
<link rel="stylesheet" href="https://fonts.googleapis.com/css2?family=Montserrat:wght@400;500;600;700&display=swap">
<style>
  :root {
    --page-bg: #f4f4f4;
    --card-bg: #ffffff;
    --ink: #000000;
    --brand-teal: #3a7b74;
    --rule-grey: #dcdcdc;
    --card-edge-light: #c9c9c9;
    --card-edge-dark: #222222;
    --band-text: #ffffff;
  }

  * { box-sizing: border-box; margin: 0; padding: 0; }

  html, body {
    width: 1200px;
    height: 387px;
    overflow: hidden;
    background: var(--page-bg);
    font-family: "Montserrat", "Helvetica Neue", Arial, sans-serif;
    color: var(--ink);
  }

  .stage {
    position: relative;
    width: 1200px;
    height: 387px;
  }

  .card {
    position: absolute;
    top: 16px;
    width: 565px;
    height: 358px;
    background: var(--card-bg);
    overflow: hidden;
  }

  /* Front side */
  .card--front {
    left: 16px;
    border: 1px solid var(--card-edge-light);
    box-shadow: 1px 2px 2px rgba(0, 0, 0, 0.12);
    display: flex;
    flex-direction: column;
    align-items: center;
    justify-content: center;
  }

  .front__name {
    font-weight: 400;
    font-size: 40px;
    letter-spacing: 1.5px;
    line-height: 1;
    margin-top: 12px;
  }

  .front__tagline {
    margin-top: 27px;
    font-weight: 700;
    font-size: 10.5px;
    letter-spacing: 1px;
    color: var(--brand-teal);
  }

  /* Back side */
  .card--back {
    left: 625px;
    border: 1px solid var(--card-edge-dark);
  }

  .back__header {
    position: absolute;
    left: 0;
    top: 0;
    width: 100%;
    height: 198px;
    border-bottom: 1px solid var(--rule-grey);
    display: flex;
    align-items: center;
    padding-left: 34px;
  }

  .back__brand {
    font-weight: 400;
    font-size: 39px;
    line-height: 1;
    color: var(--brand-teal);
    margin-top: -14px;
  }

  .back__contact {
    position: absolute;
    left: 315px;
    top: 224px;
    line-height: 1.25;
  }

  .contact__name {
    font-weight: 600;
    font-size: 17px;
    letter-spacing: 0.3px;
  }

  .contact__title,
  .contact__line {
    font-weight: 500;
    font-size: 12.5px;
  }

  .back__band {
    position: absolute;
    left: 0;
    bottom: 0;
    width: 100%;
    height: 31px;
    background: var(--brand-teal);
    color: var(--band-text);
    font-weight: 500;
    font-size: 13px;
    display: flex;
    align-items: center;
    justify-content: center;
  }
</style>
</head>
<body>
  <main class="stage">
    <section class="card card--front" aria-label="Card front">
      <h1 class="front__name">QUELBROOK INSIGHTS</h1>
      <p class="front__tagline">MEASURE , MONITOR , SAVE</p>
    </section>

    <section class="card card--back" aria-label="Card back">
      <header class="back__header">
        <p class="back__brand">Quelbrook Insights</p>
      </header>

      <address class="back__contact" style="font-style: normal;">
        <p class="contact__name">FIRST NAME LAST NAME</p>
        <p class="contact__title">TITLE</p>
        <p class="contact__line">Address goes here</p>
        <p class="contact__line">+61-400-000-000</p>
      </address>

      <footer class="back__band">www.quelbrook-insights.example</footer>
    </section>
  </main>
</body>
</html>
```